Law Firm Advertising Design Needed

Law Office of Dalmer K Quoss provides legal services to businesses and individuals who have been or are being injured. Our main practice area is personal injury (car accidents, wrongful death, premises liability), but we are looking for an ad that highlights a lesser known area of our practice - insurance company bad faith and breach of contract.

This ad will be placed in 8 1/2" x 11" format in a local neighborhood directory. It will also be placed in a smaller format (to be determined) in the local newspaper of a region of Arizona that has recently lost a considerable number of homes and people to wildfire.

We want to convey through the ad that our firm is available to help if their insurance company is not paying a legitimate claim or not paying enough for their claim.

Because of the tragic nature of the events in Velmont, we would like to avoid images of fire or anything resembling fire. However, the ad should capture the attention of individuals who are struggling through an insurance claim with all the stacks of paperwork and frustrated with unresponsive adjusters and unreasonably low offers.

The design should convey a feeling of safety, security and being taken care of.

Information that must be included in the ad are: the firm name (Law Office of Dalmer K Quoss), address (47390 N 18th Street, Ste 506, Phoenix, AZ 85044), the phone number (602-514-7730) and the fact that we have mobile offices available to assist in your area.

An example of text that has been used in the past is here:
"If your own insurance company is refusing to pay what you are owed on a claim, call the Law Office of Dalmer K Quoss. We fight for you by examining the reasons your insurance carrier is denying or making an insufficient offer on the claim; updating and correcting claim documentation; making a new demand and filing a lawsuit if necessary. Whether it's a simple misunderstanding or something more complicated, we can help!

Here are a few of the kinds of claims we handle:
- Hit and Run or Uninsured driver claims
- Fire, flood and property loss
- Life insurance benefits
- Health insurance claims
- Catastrophic losses
- Business insurance
- Wrongful Death Benefits

Our attorneys are available to help you cut through the nonsense. Call to make an appointment for a free consultation with an attorney today. "

An example of a previous ad for car accident services is attached for reference.
Updates

Hi Everyone,

The main lawyer involved in the decision making process has been giving me some feedback in general on the designs that I thought I would pass along.  He does not want the name of the law firm to be the first thing you notice when you look at the ad. Try to keep that small and possibly to the bottom of the ad. The phone number should be rather large, but the address should be rather small (we are required by the Lawyers' Guild to include our address, but we don't want our location to limit the location of our clients because our mobile offices can travel to them).  He would prefer that the logo either not be included or be not a significant part of the ad.

                                   

Thanks!  I will continue providing individual feedback to ads received. 

Target Market(s)

Low to middle income residents of the State of Arizona with little or no college education

Industry/Entity Type

Insurance

```html
<!DOCTYPE html>
<html lang="en">
<head>
<meta charset="utf-8">
<title>Law Office of Dalmer K. Quoss – Insurance Claims Flyer</title>
<link href="https://fonts.googleapis.com/css2?family=Anton&family=Arimo:wght@400;700&display=swap" rel="stylesheet">
<style>
  :root {
    --paper: #ffffff;
    --ink: #1a1a1a;
    --band: #000000;
    --grey: #a3a3a3;
    --rule: #9a9a9a;
    --photo-a: #3a2a22;
    --photo-b: #15181f;
    --wood-a: #8a5a33;
    --wood-b: #5e3a1e;
  }
  * { margin: 0; padding: 0; box-sizing: border-box; }
  html, body { width: 956px; height: 1200px; overflow: hidden; background: #ececec; }
  .flyer {
    position: relative; width: 956px; height: 1200px;
    background: var(--paper); color: var(--ink);
    font-family: "Arimo", Arial, sans-serif; overflow: hidden;
  }
  .shapes { position: absolute; inset: 0; }
  .title {
    position: absolute; left: 580px; top: 190px; width: 330px;
    text-align: center; font-family: "Anton", Impact, sans-serif;
    font-size: 42px; line-height: 52px; font-weight: 400; color: #fff;
    transform: skewX(-8deg);
    -webkit-text-stroke: 1.5px #111;
    text-shadow: 0 0 8px rgba(255,255,255,.9), 2px 2px 0 #111;
  }
  .intro {
    position: absolute; left: 33px; top: 488px; width: 404px;
    font-size: 17.5px; line-height: 33.5px; text-align: justify;
  }
  .divider { position: absolute; left: 473px; top: 492px; width: 1px; height: 322px; background: var(--rule); }
  .claims { position: absolute; left: 500px; top: 490px; }
  .claims h2 { font-size: 28px; font-weight: 700; margin-bottom: 16px; }
  .claims ul { list-style: none; padding-left: 10px; }
  .claims li { font-size: 21.5px; line-height: 39.5px; }
  .claims li::before { content: "• "; }
  .contact-band { position: absolute; left: 0; top: 836px; width: 956px; height: 150px; background: var(--band); }
  .brand-box {
    position: absolute; left: 354px; top: 841px; width: 148px; height: 140px;
    background: #fff; display: flex; align-items: center; justify-content: center;
    font-size: 24px; font-weight: 400; color: var(--ink);
  }
  .contact { position: absolute; left: 560px; top: 846px; color: #fff; font-style: normal; }
  .contact h3 { font-size: 22px; font-weight: 400; margin-bottom: 6px; }
  .contact .address { font-size: 15px; line-height: 22px; }
  .contact .phone { font-size: 38px; font-weight: 700; line-height: 48px; margin-top: 4px; }
  .gavel {
    position: absolute; left: 80px; top: 872px; width: 200px; height: 150px;
    border-radius: 30px;
    background: radial-gradient(ellipse at 50% 45%, var(--wood-a), var(--wood-b));
  }
  .firm-name {
    position: absolute; left: 34px; top: 1085px; width: 290px;
    font-size: 24px; font-weight: 700; line-height: 34px; text-align: center;
  }
  .mobile { position: absolute; left: 352px; top: 1018px; font-size: 21.5px; line-height: 27px; }
  .cta { position: absolute; left: 352px; top: 1084px; width: 580px; font-size: 22.5px; line-height: 30px; }
</style>
</head>
<body>
<main class="flyer">
  <svg class="shapes" width="956" height="1200" viewBox="0 0 956 1200">
    <defs>
      <radialGradient id="photoTone" cx="45%" cy="40%" r="70%">
        <stop offset="0" stop-color="var(--photo-a)"/>
        <stop offset="1" stop-color="var(--photo-b)"/>
      </radialGradient>
    </defs>
    <circle cx="272" cy="178" r="300" fill="var(--grey)"/>
    <circle cx="742" cy="258" r="204" fill="var(--grey)"/>
    <circle cx="272" cy="178" r="282" fill="#fff"/>
    <circle cx="272" cy="178" r="272" fill="url(#photoTone)" role="img" aria-label="Portrait photo of the attorney in a suit seated at his desk in his office"/>
  </svg>

  <h1 class="title">Law Office<br>of Dalmer<br>K. Quoss</h1>

  <p class="intro">If your own insurance company is refusing to pay what you are owed on a claim, call the Law Office of Dalmer K Quoss. We fight for you by examining the reasons your insurance carrier is denying or making an insufficient offer on the claim; updating and correcting claim documentation; making a new demand and filing a lawsuit if necessary. Whether it's a simple misunderstanding or something more complicated, we can help!</p>

  <div class="divider"></div>

  <section class="claims">
    <h2>Kinds Of Claims We Handle</h2>
    <ul>
      <li>Hit and Run or Uninsured driver claims</li>
      <li>Fire, flood and property loss</li>
      <li>Life insurance benefits</li>
      <li>Health insurance claims</li>
      <li>Catastrophic losses</li>
      <li>Business insurance</li>
      <li>Wrongful Death Benefits</li>
    </ul>
  </section>

  <div class="contact-band"></div>
  <div class="brand-box">Quoss Law</div>
  <address class="contact">
    <h3>Contact Info:</h3>
    <p class="address">47390 N 18th Street, Ste 506, Phoenix, AZ 85044</p>
    <p class="phone">P: 602-514-7730</p>
  </address>

  <div class="gavel" role="img" aria-label="Illustration of a wooden gavel resting on a round sound block labelled law"></div>

  <p class="firm-name">The Law Office<br>of Dalmer K. Quoss</p>
  <p class="mobile">We Have Mobile Offices Available<br>To Assist In Your Area</p>
  <p class="cta">Our attorneys are available to help you cut through the nonsense. Call to make an appointment for a free consultation with an attorney today.</p>
</main>
</body>
</html>
```